Business Cards Design for the electrical wholesaler: clean bold dynamic :)

We need a business card design that would follow our latest brand guidelines. As an electrical wholesaler we want to bring a fresh look and feel into the industry. The design should be clean bold and dynamic. It should come alive with the renewed energy of our green colour. Our grey colour should keep things balanced and complement the notion of maturity and responsibility. We employ Lato as a corporate font however are not bound by this font and we’re open to interpretation here.

Target Market(s)

Electrical contractors

Industry/Entity Type

Business

Contact Information for Business Card

Logo
Name & Surname: Halyna Dorosh
Job Title: Director of Marketing
Email: halya.dorosh@quillmail.example
Cell phone: XXX.XXX.XXXX
Address: 20517 - 87 Ave. Edmonton, AB, Canada. T6K 4N8
Business Phone: 780.555.0184
Website: www.brovix.example

Font styles to use
Other font styles liked:
• Lato

Requirements
Must have
• Logo & website
Nice to have
• Brand elements - some of them you may find in the attached Brand Guidelines (e.g. three lines on the background signifying "W")

```html
<!DOCTYPE html>
<html lang="en">
<head>
<meta charset="utf-8">
<title>brovix business cards</title>
<link rel="stylesheet" href="https://fonts.googleapis.com/css2?family=Oswald:wght@500&family=Work+Sans:wght@400;500;600&display=swap">
<style>
  :root {
    --brand-green: #8cc63f;
    --brand-green-deep: #7fbf36;
    --brand-grey: #4d4d4f;
    --text-grey: #3d3d3f;
    --card-white: #ffffff;
    --backdrop: #e9e9e7;
  }
  * { margin: 0; padding: 0; box-sizing: border-box; }
  html, body {
    width: 1200px; height: 930px; overflow: hidden;
    background: var(--backdrop);
    font-family: "Work Sans", sans-serif;
  }
  .canvas { position: relative; width: 1200px; height: 930px; }
  .card {
    position: absolute; width: 560px; height: 320px;
    box-shadow: 0 2px 10px rgba(0,0,0,0.12);
  }

  /* Front */
  .card-front {
    left: 90px; top: 110px;
    background: linear-gradient(135deg, var(--brand-green) 0%, #9ccf4c 100%);
    color: var(--card-white);
  }
  .card-front .wordmark {
    position: absolute; left: 0; right: 0; top: 96px;
    display: flex; flex-direction: column; align-items: center;
  }
  .lockup { display: flex; align-items: center; gap: 14px; }
  .lockup .dot { width: 34px; height: 34px; border-radius: 50%; }
  .lockup .name { font-weight: 600; font-size: 64px; line-height: 1; letter-spacing: -1px; }
  .card-front .dot { background: var(--card-white); }
  .tagline {
    font-weight: 500; font-size: 11px; letter-spacing: 2.4px;
    text-transform: uppercase; margin-top: 8px; margin-left: 48px;
  }
  .card-front .website {
    position: absolute; left: 0; right: 0; bottom: 34px;
    text-align: center; font-size: 14px; letter-spacing: 0.5px;
  }

  /* Back */
  .card-back {
    left: 550px; top: 500px;
    background: var(--card-white);
    color: var(--text-grey);
  }
  .card-back .wordmark { position: absolute; left: 150px; top: 44px; }
  .card-back .dot { background: var(--brand-green); }
  .card-back .lockup .name { color: var(--brand-grey); font-size: 56px; }
  .card-back .tagline { color: var(--brand-grey); margin-left: 48px; }

  .person {
    position: absolute; right: 310px; top: 168px; text-align: right;
  }
  .person-name {
    font-family: "Oswald", sans-serif; font-weight: 500;
    font-size: 30px; line-height: 1; color: var(--brand-green-deep);
    text-transform: uppercase; letter-spacing: 0.5px;
  }
  .person-title { font-size: 14px; margin-top: 4px; }

  .divider {
    position: absolute; left: 268px; top: 160px;
    width: 1.5px; height: 60px; background: var(--brand-green);
  }
  .contacts {
    position: absolute; left: 288px; top: 158px;
    list-style: none; font-size: 12.5px; line-height: 21px;
  }
  .contacts li { display: flex; align-items: center; gap: 8px; }
  .contacts svg { width: 10px; height: 10px; flex: none; }
  .contacts .accent { color: var(--brand-green-deep); }

  .address {
    position: absolute; left: 0; right: 0; bottom: 34px;
    text-align: center; font-size: 13px; letter-spacing: 0.3px;
  }
</style>
</head>
<body>
<main class="canvas">

  <section class="card card-front" aria-label="Card front">
    <div class="wordmark">
      <div class="lockup"><span class="dot"></span><span class="name">brovix</span></div>
      <div class="tagline">Electrical Wholesalers</div>
    </div>
    <div class="website">www.brovix.example</div>
  </section>

  <section class="card card-back" aria-label="Card back">
    <div class="wordmark">
      <div class="lockup"><span class="dot"></span><span class="name">brovix</span></div>
      <div class="tagline">Electrical Wholesalers</div>
    </div>

    <div class="person">
      <div class="person-name">Halyna Dorosh</div>
      <div class="person-title">Founder</div>
    </div>

    <div class="divider"></div>

    <ul class="contacts">
      <li>
        <svg viewBox="0 0 10 10" aria-hidden="true"><path d="M2 0.8 L3.6 2.8 L2.8 3.8 Q4 6.2 6.2 7.2 L7.2 6.4 L9.2 8 L8.2 9.4 Q3.5 9 0.6 1.8 Z" fill="#8cc63f"/></svg>
        <span>780.555.0184</span>
      </li>
      <li>
        <svg viewBox="0 0 10 10" aria-hidden="true"><rect x="0.8" y="2" width="8.4" height="6" fill="none" stroke="#8cc63f" stroke-width="1.2"/><path d="M0.8 2 L5 5.4 L9.2 2" fill="none" stroke="#8cc63f" stroke-width="1.2"/></svg>
        <span>halya.dorosh@quillmail.example</span>
      </li>
      <li>
        <svg viewBox="0 0 10 10" aria-hidden="true"><circle cx="5" cy="5" r="4.2" fill="none" stroke="#8cc63f" stroke-width="1.1"/><ellipse cx="5" cy="5" rx="1.8" ry="4.2" fill="none" stroke="#8cc63f" stroke-width="0.9"/><path d="M0.8 5 H9.2" stroke="#8cc63f" stroke-width="0.9"/></svg>
        <span>www.<span class="accent">brovix</span>.example</span>
      </li>
    </ul>

    <div class="address">20517 - 87 Ave. Edmonton, AB, Canada. T6K 4N8</div>
  </section>

</main>
</body>
</html>
```